Pebble Pete''s Funhouse Website Revamp

We have a children's entertainment center that hasn't changed in 20 years and the site looks like it was created 20 years ago. We need a new, modern, clean site that pops. Attached is the new logo that should be used as a style guide.

Current site is: www.pebblepetesfun-example.com

Thanks!
Updates

Designers, thank you all for the amazing work. It was exciting to be able to go through and see all the creativity that came in. I have decided on a design but wanted to share my thanks and appreciation for your time. Warm regards, Morris

Target Market(s)

Mothers with children in the 2 - 14 range.

Industry/Entity Type

Entertainment

```html
<!DOCTYPE html>
<html lang="en">
<head>
<meta charset="utf-8">
<title>Pebble Pete's Funhouse</title>
<link href="https://fonts.googleapis.com/css2?family=Roboto:ital,wght@0,400;0,500;0,700;1,400&family=Courgette&family=Montserrat:wght@400;500&display=swap" rel="stylesheet">
<style>
:root{
  --purple:#8a3a9b;--teal:#0db8bf;--teal-dark:#0aa6ad;--red:#e01b1b;--green:#27a830;
  --orange:#f0712a;--sky:#00b1e6;--lime:#7ab648;--pink:#e5195a;--navy:#0f1a33;
  --title-blue:#1c5fae;--text:#555;--white:#fff;
}
*{box-sizing:border-box;margin:0;padding:0}
html,body{width:1071px;height:1200px;overflow:hidden}
body{position:relative;font-family:'Roboto',sans-serif;color:var(--text);
  background:
    radial-gradient(circle at 290px 90px,rgba(245,130,40,.75),transparent 140px),
    radial-gradient(circle at 60px 950px,rgba(150,200,40,.9),transparent 200px),
    radial-gradient(circle at 1010px 900px,rgba(150,200,40,.9),transparent 200px),
    radial-gradient(circle at 530px 950px,rgba(240,150,60,.5),transparent 180px),
    radial-gradient(circle at 1000px 280px,rgba(250,220,80,.5),transparent 120px),
    linear-gradient(#a9d6f0 0,#cde7f3 520px,#d6e9c8 700px,#b9d85a 900px,#c5dd3a 1200px);}
.topbar{position:absolute;left:0;top:0;width:100%;height:4px;background:var(--purple)}
.logo{position:absolute;left:161px;top:8px;width:162px;height:92px;background:var(--white);
  border-radius:46px;display:flex;align-items:center;justify-content:center;gap:6px;
  box-shadow:0 2px 6px rgba(0,0,0,.08)}
.logo span.mark{width:12px;height:12px;border-radius:50%;background:var(--orange);flex-shrink:0}
.logo b{font-family:'Montserrat',sans-serif;font-weight:500;font-size:12px;color:var(--green)}
.join{position:absolute;left:813px;top:36px;width:80px;height:20px;background:var(--lime);
  color:#fff;font-size:9px;display:flex;align-items:center;justify-content:center}
.search{position:absolute;left:635px;top:73px;width:134px;height:18px;background:#fff;border:1px solid #ccc;
  font-size:8px;color:#999;padding:4px 6px}
.search-btn{position:absolute;left:769px;top:73px;width:19px;height:18px;background:#444}
.social{position:absolute;top:73px;display:flex;gap:1px;left:790px}
.social i{display:block;width:19px;height:18px}
nav{position:absolute;left:161px;top:105px;width:749px;height:46px;display:flex}
nav a{flex:1;display:flex;align-items:center;justify-content:center;color:#fff;font-size:10px;text-decoration:none}
.slider{position:absolute;left:161px;top:159px;width:749px;height:335px;border:5px solid var(--teal)}
.slider .photo{width:100%;height:100%;
  background:linear-gradient(180deg,#3e8a3c 0,#2f6e3a 45%,#8d6a2a 62%,#d98a22 80%,#6b5a3a 100%)}
.arrow{position:absolute;top:145px;width:30px;height:30px;border-radius:50%;background:rgba(0,0,0,.25)}
.dots{position:absolute;left:313px;bottom:0;width:123px;height:22px;background:var(--teal);
  display:flex;align-items:center;justify-content:center;gap:6px}
.dots i{width:8px;height:8px;border-radius:50%;background:#e8e8e8}
.dots i:first-child{background:#e6606a}
.welcome{position:absolute;left:180px;top:516px;width:710px;text-align:center}
.welcome h1{font-family:'Courgette',cursive;font-weight:400;font-size:19px;color:var(--title-blue)}
.welcome p{font-size:8.6px;line-height:17px;margin-top:6px}
.btn-read{position:absolute;left:479px;top:628px;width:113px;height:26px;background:var(--teal);color:#fff;
  font-size:10px;font-style:italic;display:flex;align-items:center;justify-content:center}
.tile{position:absolute;top:704px;height:162px}
.tile .photo{height:135px}
.tile .cap{height:27px;display:flex;align-items:center;justify-content:space-between;gap:6px;padding:0 8px;
  color:#fff;font-family:'Montserrat',sans-serif;font-size:10.5px;letter-spacing:-.2px;white-space:nowrap}
.plus{width:15px;height:15px;border-radius:50%;background:#fff;position:relative;flex-shrink:0}
.plus:before,.plus:after{content:"";position:absolute;left:3px;top:6.5px;width:9px;height:2px;background:#999}
.plus:after{transform:rotate(90deg)}
.offers{position:absolute;left:658px;top:704px;width:233px;height:162px;background:var(--teal);padding:12px;color:#fff}
.offers h2{font-family:'Montserrat',sans-serif;font-weight:400;font-size:16px;color:#1a1a1a}
.offers p{font-family:'Montserrat',sans-serif;font-size:7.5px;line-height:13px;margin-top:8px;width:120px}
.offers .coins{position:absolute;left:140px;top:22px;width:70px;height:80px;background:radial-gradient(#f5d33a,#d9a615 60%,transparent 70%)}
.offers .click{position:absolute;left:125px;top:120px;width:93px;height:30px;background:var(--red);
  font-family:'Montserrat',sans-serif;font-size:10px;display:flex;align-items:center;justify-content:center}
.lower{position:absolute;left:161px;top:900px;width:749px;height:242px;background:var(--teal);color:#fff}
.lower h3{font-family:'Courgette',cursive;font-weight:400;font-size:16px;position:absolute}
.lower .small{font-size:8px;position:absolute}
.vid{position:absolute;left:233px;width:270px;height:62px}
.vid .thumb{position:absolute;left:0;top:0;width:67px;height:62px}
.vid b{position:absolute;left:79px;top:8px;font-size:8.5px}
.vid p{position:absolute;left:79px;top:24px;font-size:7.5px;color:#d84a3a;line-height:10px;width:180px}
.vid em{position:absolute;left:79px;top:52px;font-size:8px;color:var(--pink);font-style:normal}
footer{position:absolute;left:0;top:1142px;width:100%;height:58px;background:var(--navy);color:#fff}
footer .copy{position:absolute;left:177px;top:24px;font-size:8.5px}
footer .icons{position:absolute;left:758px;top:17px;display:flex;gap:15px}
footer .icons i{width:22px;height:22px;display:block}
</style>
</head>
<body>
<div class="topbar"></div>
<div class="logo"><span class="mark"></span><b>Pebble Pete's Funhouse</b></div>
<div class="join">Join Us</div>
<div class="search">Search</div>
<div class="search-btn"><svg width="19" height="18"><circle cx="9" cy="8" r="3.2" fill="none" stroke="#fff" stroke-width="1.4"/><line x1="11.3" y1="10.3" x2="13.5" y2="12.5" stroke="#fff" stroke-width="1.4"/></svg></div>
<div class="social" aria-label="Social links">
  <i style="background:#2ba3e0"></i><i style="background:#2c4a8c"></i><i style="background:#e9457e"></i><i style="background:#0a6aaa"></i><i style="background:#f7a51c"></i>
</div>
<nav>
  <a style="background:var(--red)">Home</a>
  <a style="background:var(--green)">Attractions</a>
  <a style="background:var(--orange)">Parties</a>
  <a style="background:var(--sky)">Directions</a>
  <a style="background:var(--lime)">Contact Us</a>
</nav>
<div class="slider">
  <div class="photo" role="img" aria-label="Children riding bumper cars in a jungle themed play hall"></div>
  <span class="arrow" style="left:40px"></span><span class="arrow" style="right:40px"></span>
  <div class="dots"><i></i><i></i><i></i><i></i><i></i></div>
</div>
<section class="welcome">
  <h1>Welcome To Our Website</h1>
  <p>Lorem ipsum dolor sit amet, consectetuer adipiscing elit, sed diam nonummy nibh euismod tincidunt ut laoreet dolore magna aliquam erat volutpat. Lorem ipsum dolor sit amet, consectetuer adipiscing elit, sed diam nonummy nibh euismod tincidunt ut laoreet dolore magna aliquam erat volutpat. Lorem ipsum dolor sit amet, consectetuer adipiscing elit, sed diam nonummy nibh euismod tincidunt ut laoreet dolore magna aliquam erat volutpat. Lorem ipsum dolor sit amet, consectetuer adipiscing elit, sed diam nonummy nibh euismod tincidunt ut laoreet dolore magna aliquam erat volutpat.</p>
</section>
<div class="btn-read">Read More +</div>
<div class="tile" style="left:178px;width:233px">
  <div class="photo" role="img" aria-label="Child on a red airplane ride" style="background:linear-gradient(180deg,#c8a070 0,#b84a2a 40%,#d84a2a 55%,#3c8fb0 100%)"></div>
  <div class="cap" style="background:var(--pink)"><span>Pebble Pete's is ideal for</span><span class="plus"></span></div>
</div>
<div class="tile" style="left:418px;width:234px">
  <div class="photo" role="img" aria-label="Kids cheering on a green slide ride" style="background:linear-gradient(180deg,#d8d0b8 0,#6aa060 35%,#2f8a3a 65%,#a8d090 100%)"></div>
  <div class="cap" style="background:var(--orange)"><span>Driving distance to Pebble Pete's</span><span class="plus"></span></div>
</div>
<div class="offers">
  <h2>Online Offers</h2>
  <p>Lorem ipsum dolor sit amet, consectetuer adipiscing elit, sed diam nonummy nibh euismod tincidunt ut laoreet orem ipsum dolor sit amet, consectetuer adipiscing quam erat volutpat.</p>
  <div class="coins" role="img" aria-label="Stacks of gold coins"></div>
  <div class="click">Click Here</div>
</div>
<section class="lower">
  <h3 style="left:17px;top:12px">Shows</h3>
  <span class="small" style="left:206px;top:18px">‹ ›</span>
  <div role="img" aria-label="Birthday party room with balloons" style="position:absolute;left:17px;top:53px;width:200px;height:84px;background:linear-gradient(180deg,#e8c24a 0,#5d9a4a 45%,#4a7a3a 75%,#8a4a2a 100%)"></div>
  <p style="position:absolute;left:17px;top:146px;width:200px;font-size:8.5px;line-height:17px">The management consulting firm the world's business leaders come to when they want</p>
  <span class="small" style="left:17px;top:185px;color:#111">Read More +</span>
  <h3 style="left:233px;top:12px">Videos</h3>
  <span class="small" style="left:448px;top:31px;color:#111">View more +</span>
  <div class="vid" style="top:54px">
    <div class="thumb" role="img" aria-label="Indoor play structure" style="background:linear-gradient(135deg,#2a4a8a,#e0b030)"></div>
    <b>SUSPENDISSE MATTIS TELI</b><p>Suspendisse mattis tellus vel augue mollis ultrices suspends</p><em>Read More +</em>
  </div>
  <div class="vid" style="top:132px">
    <div class="thumb" role="img" aria-label="Guitar close-up" style="background:linear-gradient(135deg,#3a2a1a,#e09a30)"></div>
    <b>SUSPENDISSE MATTIS TELI</b><p>Suspendisse mattis tellus vel augue mollis ultrices suspends</p><em>Read More +</em>
  </div>
  <h3 style="left:529px;top:10px;color:var(--title-blue)">Happy Clients Says</h3>
  <span class="small" style="left:721px;top:16px">‹ ›</span>
  <div role="img" aria-label="Client portrait" style="position:absolute;left:593px;top:56px;width:60px;height:60px;border-radius:50%;background:#e8c8a8;border:2px solid #fff"></div>
  <p style="position:absolute;left:520px;top:124px;width:205px;text-align:center;font-size:10px;line-height:17px">Donec sed odio dui. Nullam id dolor id nibh ultricies vehicula ut id elit. Sollicitudin Lorem Egestas Dapibus.</p>
  <span style="position:absolute;left:651px;top:196px;font-size:9.5px;color:#111">Mr.Dale, Manager</span>
</section>
<footer>
  <span class="copy">COPYRIGHT © 2014 The Funhouse ALL RIGHTS RESERVED.</span>
  <div class="icons" aria-label="Social links"><i style="background:#3b5a9a"></i><i style="background:#5a6c80"></i><i style="background:#2aa9e0"></i><i style="background:#e0342a"></i></div>
</footer>
</body>
</html>
```